Tide & Thistle Website Creation For Online Spirits Sales via MerrowVats.com

Want a Website developed that I will use to partner with Merrow Vats to sell my signature rum online. Merrow Vats will add the final code to make the website an e-commerce site. Website should have links to Social media pages, recipies, About, news and events, products. I have he domain name already just need a designer to make the website look professional. Need website capable of being viewed on iPhone and Android devices. Please use the color scheme that is on the label. The brand motto is: Celebrate Life With Family old and new friends. The bottle sent in the images will be replaced with and actual high resolution image of the bottle when it is produce on 27 DEC 21. Can give the selected designer access to develop the website. I have the hostbramble.com domain name. Final code will be added by a designer from MerrowVats.com to make it a e-commerce store.
Updates

I added more information to refine the design I wanted. I should have had this information available to the designers when I started the project.

Target Market(s)

Target Market is 25-50 year old who drink rum

Industry/Entity Type

Spirits. Using Website to sell Rum online

Number of Pages Required

1 page

Font styles to use
Sans Serif

Colors
00AB8E
00BBA5
67D7C9
C6EFE9
E9F9F6

Requirements
Must have
• Must look elegant and of high class. Rum is being market as a premium unnamed rum.
Nice to have
• Video of people drinking, smiling and celebrating

```html
<!DOCTYPE html>
<html lang="en">
<head>
<meta charset="utf-8">
<title>Tide &amp; Thistle — Premium Rum</title>
<link href="https://fonts.googleapis.com/css2?family=Playfair+Display:wght@700;900&family=Roboto:wght@400;500;700&display=swap" rel="stylesheet">
<style>
:root{
  --teal:#00AB8E;
  --teal-2:#00BBA5;
  --teal-3:#67D7C9;
  --teal-4:#C6EFE9;
  --teal-5:#E9F9F6;
  --ink:#1c1c1c;
  --text:#555;
  --muted:#888;
  --footer:#232323;
  --footer-bar:#1a1a1a;
  --gold:#f3b61f;
  --white:#fff;
}
*{box-sizing:border-box;margin:0;padding:0}
html,body{width:1200px;height:3576px;overflow:hidden}
body{position:relative;background:var(--white);font-family:'Roboto',sans-serif;color:var(--text);font-size:14px;line-height:1.6}
.serif{font-family:'Playfair Display',serif}
.abs{position:absolute}
a{color:inherit;text-decoration:none}

/* Header */
.site-header{position:absolute;left:0;top:0;width:1200px;height:112px;background:var(--white)}
.brand{position:absolute;left:40px;top:30px;display:flex;align-items:center;gap:12px}
.brand-mark{width:44px;height:44px;border-radius:50%;background:var(--ink)}
.brand-name{font-family:'Playfair Display',serif;font-weight:700;font-size:26px;color:var(--ink);letter-spacing:1px}
.welcome{position:absolute;left:340px;top:10px;font-size:12px;font-weight:500;color:var(--teal);letter-spacing:.5px}
.header-divider{position:absolute;left:340px;top:44px;width:820px;height:1px;background:#e6e6e6}
.utility{position:absolute;right:40px;top:8px;display:flex;gap:34px;font-size:12px;color:var(--ink);align-items:center}
.flag{display:inline-block;width:20px;height:13px;background:linear-gradient(#b22 0 33%,#fff 33% 66%,#33a 66%);vertical-align:middle;margin-right:8px}
.main-nav{position:absolute;left:340px;top:64px;display:flex;gap:36px;font-size:13px;font-weight:700;color:var(--ink);letter-spacing:.3px}
.main-nav .active{color:var(--teal);border-bottom:2px solid var(--teal);padding-bottom:6px}

/* Hero */
.hero{position:absolute;left:0;top:112px;width:1200px;height:600px;background:radial-gradient(ellipse at 30% 40%,#7a5236 0%,#3a261a 40%,#150e0a 80%)}
.hero-title{position:absolute;left:0;top:396px;width:1200px;text-align:center;font-family:'Playfair Display',serif;font-weight:900;font-size:36px;line-height:1.4;color:var(--white);letter-spacing:1.5px;text-transform:uppercase}
.hero-dots{position:absolute;right:24px;top:236px;display:flex;flex-direction:column;gap:10px}
.hero-dots span{width:9px;height:9px;border-radius:50%;background:rgba(255,255,255,.6)}
.hero-dots span:first-child{background:var(--white)}

/* Product */
.product{position:absolute;left:0;top:712px;width:1200px;height:736px}
.product-shot{position:absolute;left:112px;top:100px;width:390px;height:528px;border:1px solid #e4e4e4;background:var(--white)}
.bottle{position:absolute;left:150px;top:60px;width:90px;height:400px;border-radius:20px 20px 10px 10px;background:linear-gradient(90deg,#8a5a1e,#c98a3a 45%,#7a4c16)}
.product-info{position:absolute;left:620px;top:128px;width:480px}
.section-title{font-family:'Playfair Display',serif;font-weight:900;font-size:30px;color:var(--ink);letter-spacing:1px;text-transform:uppercase}
.title-rule{width:200px;height:2px;background:var(--teal);margin:6px 0 20px}
.tick-list{list-style:none;font-size:12.5px}
.tick-list li{display:flex;gap:12px;margin-bottom:14px}
.tick-list svg{flex:none;margin-top:3px}
.rating{display:flex;align-items:center;gap:14px;margin-top:16px;font-size:11px;color:var(--teal);font-weight:700}
.stars{color:var(--gold);font-size:15px;letter-spacing:2px}
.price{margin-top:10px;display:flex;align-items:baseline;gap:22px}
.price-now{font-size:34px;font-weight:700;color:var(--teal)}
.price-was{font-size:20px;color:#aaa;text-decoration:line-through}
.stock{margin-top:10px;font-size:12px;font-weight:700;color:var(--ink);display:flex;gap:30px}
.desc{margin-top:14px;font-size:12.5px;width:440px}
.buy-row{margin-top:26px;display:flex;gap:16px}
.qty{display:flex;border:1px solid #ddd;height:46px}
.qty span{width:40px;display:flex;align-items:center;justify-content:center;color:var(--ink);font-weight:700}
.qty span+span{border-left:1px solid #ddd}
.btn-cart{background:var(--teal);color:var(--white);font-size:12px;font-weight:700;padding:0 22px;display:flex;align-items:center;gap:10px;height:46px}

/* About */
.about{position:absolute;left:0;top:1448px;width:1200px;height:592px;background:linear-gradient(120deg,#008f77,var(--teal) 45%,var(--teal-2))}
.about-photo-a{position:absolute;left:112px;top:80px;width:340px;height:232px;background:linear-gradient(135deg,#c7b8a3,#7c6856)}
.about-photo-b{position:absolute;left:196px;top:212px;width:344px;height:252px;border:5px solid var(--white);background:linear-gradient(135deg,#5a3a4f,#1e1420)}
.about-text{position:absolute;left:660px;top:136px;width:440px;color:var(--white)}
.about-text .section-title{color:var(--white)}
.about-text .title-rule{background:var(--white);width:140px}
.about-text p{font-size:13px;line-height:1.75}
.btn-dark{display:inline-block;margin-top:30px;background:#1d2a28;color:var(--white);font-size:12px;font-weight:700;padding:12px 26px;letter-spacing:.5px}

/* News */
.news{position:absolute;left:0;top:2040px;width:1200px;height:692px}
.news .section-title{position:absolute;top:76px;width:1200px;text-align:center}
.news-card{position:absolute;top:160px;width:312px}
.news-photo{height:228px}
.news-card h3{margin-top:28px;font-size:14px;font-weight:700;color:var(--ink)}
.news-card .rule{width:40px;height:2px;background:var(--teal);margin:6px 0 10px}
.news-card p{font-size:12px;line-height:1.6}
.news-meta{margin-top:16px;border-top:1px solid #eee;padding-top:12px;display:flex;gap:48px;font-size:11px;color:var(--muted)}
.news-meta span{display:flex;align-items:center;gap:8px}

/* Testimonials */
.reviews{position:absolute;left:0;top:2732px;width:1200px;height:428px;background:linear-gradient(120deg,#009d83,var(--teal) 50%,var(--teal-2))}
.reviews .section-title{position:absolute;top:62px;width:1200px;text-align:center;color:var(--white)}
.review{position:absolute;top:140px;width:312px}
.review-card{background:var(--white);height:150px;padding:22px 20px;font-size:12px;line-height:1.6;position:relative}
.review-card .quote{position:absolute;right:18px;bottom:8px;font-family:'Playfair Display',serif;font-size:44px;color:var(--teal);line-height:1}
.review-author{margin-top:30px;display:flex;align-items:center;gap:12px;color:var(--white)}
.avatar{width:48px;height:48px;border-radius:50%;background:var(--teal-4);border:2px solid var(--white)}
.review-author b{display:block;font-size:12px}
.review-author small{font-size:11px;opacity:.85}
.review-author .stars{margin-left:auto;font-size:13px}

/* Footer */
.site-footer{position:absolute;left:0;top:3160px;width:1200px;height:360px;background:var(--footer);color:#cfcfcf}
.footer-logo{position:absolute;left:120px;top:70px;width:200px;height:200px;border-radius:50%;border:3px solid var(--white);display:flex;align-items:center;justify-content:center;font-family:'Playfair Display',serif;font-weight:700;font-size:22px;color:var(--white)}
.footer-col{position:absolute;top:70px}
.footer-col h4{font-size:13px;font-weight:700;color:var(--white);letter-spacing:.5px}
.footer-col .rule{width:30px;height:2px;background:var(--teal);margin:8px 0 18px}
.footer-col ul{list-style:none;font-size:12px}
.footer-col li{margin-bottom:12px;display:flex;align-items:flex-start;gap:12px}
.bullet{width:5px;height:5px;border-radius:50%;background:var(--teal);margin-top:7px}
.subscribe p{font-size:12px;width:300px}
.sub-form{display:flex;margin-top:16px;width:300px;height:44px}
.sub-form span{flex:1;background:var(--white);color:#999;font-size:12px;padding:12px 16px}
.sub-form b{width:48px;background:var(--teal);display:flex;align-items:center;justify-content:center}
.socials{display:flex;gap:10px;margin-top:20px}
.socials span{width:30px;height:30px;border-radius:50%;background:var(--teal)}
.footer-bar{position:absolute;left:0;top:3520px;width:1200px;height:56px;background:var(--footer-bar);color:#aaa;font-size:12px;text-align:center;line-height:56px}
</style>
</head>
<body>

<header class="site-header">
  <div class="brand"><span class="brand-mark"></span><span class="brand-name">Tide &amp; Thistle</span></div>
  <div class="welcome">WELCOME TO TIDE &amp; THISTLE</div>
  <div class="utility"><span><i class="flag"></i>ENG ▾</span><span>USD ▾</span><span>(0) ITEMS</span></div>
  <div class="header-divider"></div>
  <nav class="main-nav">
    <a class="active">HOME</a><a>ABOUT US</a><a>OUR PRODUCTS</a><a>CATEGORIES</a><a>LATEST BLOG</a><a>REVIEWS</a><a>CONTACT US</a>
  </nav>
</header>

<section class="hero" role="img" aria-label="Friends laughing and raising glasses at a warmly lit evening gathering">
  <h1 class="hero-title">Celebrate Life With Family,<br>Old &amp; New Friends</h1>
  <div class="hero-dots"><span></span><span></span><span></span></div>
</section>

<section class="product">
  <div class="product-shot">
    <div class="bottle" role="img" aria-label="Bottle of Tide &amp; Thistle signature rum"></div>
  </div>
  <div class="product-info">
    <h2 class="section-title">Our Product</h2>
    <div class="title-rule"></div>
    <ul class="tick-list">
      <li><svg width="14" height="14" viewBox="0 0 14 14"><circle cx="7" cy="7" r="7" fill="#00AB8E"/><path d="M4 7.2l2 2 4-4.2" stroke="#fff" stroke-width="1.6" fill="none"/></svg><span>Sed ut perspiciatis unde omnis iste natus error sit voluptatem accusan tium doloremque.</span></li>
      <li><svg width="14" height="14" viewBox="0 0 14 14"><circle cx="7" cy="7" r="7" fill="#00AB8E"/><path d="M4 7.2l2 2 4-4.2" stroke="#fff" stroke-width="1.6" fill="none"/></svg><span>Sed ut perspiciatis unde omnis iste natus error sit voluptatem accusan tium doloremque.</span></li>
    </ul>
    <div class="rating"><span class="stars">★★★★★</span><span>250 REVIEWS</span></div>
    <div class="price"><span class="price-now">$ 59.00</span><span class="price-was">$ 99.00</span></div>
    <div class="stock"><span>AVAILABILITY :</span><span>IN STOCK</span></div>
    <p class="desc">Lorem ipsum dolor sit amet, consectetur adipiscing elit, sed eiusmod tempor incididunt ut labore et dolore magna aliqua. Ut enim ad minim veniam, quis nostrud exercitation ullamco.</p>
    <div class="buy-row">
      <div class="qty"><span>−</span><span>1</span><span>+</span></div>
      <div class="btn-cart">ADD TO CART
        <svg width="14" height="14" viewBox="0 0 14 14"><path d="M1 2h2l2 7h7l1.5-5H4" stroke="#fff" stroke-width="1.4" fill="none"/><circle cx="6" cy="12" r="1.2" fill="#fff"/><circle cx="11" cy="12" r="1.2" fill="#fff"/></svg>
      </div>
    </div>
  </div>
</section>

<section class="about">
  <div class="about-photo-a" role="img" aria-label="Group of friends sharing drinks at a bar"></div>
  <div class="about-photo-b" role="img" aria-label="Friends toasting at a night celebration"></div>
  <div class="about-text">
    <h2 class="section-title">About Us</h2>
    <div class="title-rule"></div>
    <p>Tide &amp; Thistle delivers premium rum through a trusted network of licensed retailers, careful shipping and attentive customer service. Our team of professionals works with partner distillers to guarantee the finest fulfillment and logistics practices, bringing each bottle from cask to your table with care and pride.</p>
    <a class="btn-dark">LEARN MORE ›</a>
  </div>
</section>

<section class="news">
  <h2 class="section-title">Latest News</h2>
  <article class="news-card" style="left:112px">
    <div class="news-photo" role="img" aria-label="Friends clinking glasses around a dinner table" style="background:linear-gradient(135deg,#b07a45,#3b2517)"></div>
    <h3>PERSPICIATIS UNDE</h3><div class="rule"></div>
    <p>Lorem ipsum dolor sit amet, consectetur adipiscing elit, sed do eiusmod tempor incididunt ut labore et dolore.</p>
    <div class="news-meta"><span>▦ Sep 01, 2021</span><span>✉ No Comments</span></div>
  </article>
  <article class="news-card" style="left:444px">
    <div class="news-photo" role="img" aria-label="Group celebrating with raised drinks at a party" style="background:linear-gradient(135deg,#8a6a55,#2a1d18)"></div>
    <h3>PERSPICIATIS UNDE</h3><div class="rule"></div>
    <p>Lorem ipsum dolor sit amet, consectetur adipiscing elit, sed do eiusmod tempor incididunt ut labore et dolore.</p>
    <div class="news-meta"><span>▦ Sep 01, 2021</span><span>✉ No Comments</span></div>
  </article>
  <article class="news-card" style="left:776px">
    <div class="news-photo" role="img" aria-label="Family toasting at a festive holiday gathering" style="background:linear-gradient(135deg,#c78a4a,#4a2414)"></div>
    <h3>PERSPICIATIS UNDE</h3><div class="rule"></div>
    <p>Lorem ipsum dolor sit amet, consectetur adipiscing elit, sed do eiusmod tempor incididunt ut labore et dolore.</p>
    <div class="news-meta"><span>▦ Sep 01, 2021</span><span>✉ No Comments</span></div>
  </article>
</section>

<section class="reviews">
  <h2 class="section-title">What Our Clients Say</h2>
  <div class="review" style="left:112px">
    <div class="review-card">Sed ut perspiciatis unde omnis iste natus error sit voluptatem accusantium doloremque laudantium, totam rem aperiam.<span class="quote">”</span></div>
    <div class="review-author"><span class="avatar"></span><div><b>NORA VELL</b><small>Businessman</small></div><span class="stars">★★★★★</span></div>
  </div>
  <div class="review" style="left:444px">
    <div class="review-card">Sed ut perspiciatis unde omnis iste natus error sit voluptatem accusantium doloremque laudantium, totam rem aperiam.<span class="quote">”</span></div>
    <div class="review-author"><span class="avatar"></span><div><b>NORA VELL</b><small>Businessman</small></div><span class="stars">★★★★★</span></div>
  </div>
  <div class="review" style="left:776px">
    <div class="review-card">Sed ut perspiciatis unde omnis iste natus error sit voluptatem accusantium doloremque laudantium, totam rem aperiam.<span class="quote">”</span></div>
    <div class="review-author"><span class="avatar"></span><div><b>NORA VELL</b><small>Businessman</small></div><span class="stars">★★★★★</span></div>
  </div>
</section>

<footer class="site-footer">
  <div class="footer-logo">Tide &amp; Thistle</div>
  <div class="footer-col" style="left:392px">
    <h4>QUICK LINKS</h4><div class="rule"></div>
    <ul>
      <li><span class="bullet"></span>Home</li>
      <li><span class="bullet"></span>About Us</li>
      <li><span class="bullet"></span>Our Products</li>
      <li><span class="bullet"></span>Reviews</li>
      <li><span class="bullet"></span>Contact Us</li>
    </ul>
  </div>
  <div class="footer-col" style="left:580px">
    <h4>CONTACT US</h4><div class="rule"></div>
    <ul>
      <li><svg width="14" height="14" viewBox="0 0 14 14"><path d="M3 1l2.5 3-1.5 1.5c.8 1.8 2 3 3.5 3.8L9 8l3 2.5-1.5 2.5C6 12.5 1.5 8 1 2.5z" fill="#00AB8E"/></svg>1-800-555-0142</li>
      <li><svg width="14" height="14" viewBox="0 0 14 14"><rect x="1" y="3" width="12" height="8" fill="none" stroke="#00AB8E" stroke-width="1.4"/><path d="M1 3l6 5 6-5" fill="none" stroke="#00AB8E" stroke-width="1.4"/></svg>hello@tidethistle.com</li>
      <li><svg width="14" height="14" viewBox="0 0 14 14"><path d="M7 13S2 8 2 5a5 5 0 0110 0c0 3-5 8-5 8z" fill="#00AB8E"/><circle cx="7" cy="5" r="1.8" fill="#232323"/></svg>PO Box 4120 Galveston,<br>United States</li>
      <li><svg width="14" height="14" viewBox="0 0 14 14"><circle cx="7" cy="7" r="5.5" fill="none" stroke="#00AB8E" stroke-width="1.4"/><path d="M1.5 7h11M7 1.5c-3 3.5-3 7.5 0 11M7 1.5c3 3.5 3 7.5 0 11" fill="none" stroke="#00AB8E" stroke-width="1.1"/></svg>www.tidethistle.com</li>
    </ul>
  </div>
  <div class="footer-col subscribe" style="left:820px">
    <h4>SUBSCRIBE NOW</h4><div class="rule"></div>
    <p>Sed ut perspiciatis unde omnis iste natus error sit voluptatem accusantium.</p>
    <div class="sub-form"><span>Email Address</span><b><svg width="16" height="16" viewBox="0 0 16 16"><path d="M1 8l14-6-5 13-2-6z" fill="#fff"/></svg></b></div>
    <div class="socials"><span></span><span></span><span></span><span></span><span></span></div>
  </div>
</footer>
<div class="footer-bar">© 2021 Tide &amp; Thistle - All Rights Reserved</div>

</body>
</html>
```